Modern Business Card

Modern professional business card with more than just logo and demographic info. Something memorable.

We are a trendy/modern chiropractic group with an emphasis on neurology, hence the minimalist-type brain logo. We want to convey that modern and technical aspect with professionalism and the elite nature of our practice environment.

```html
<!DOCTYPE html>
<html lang="en">
<head>
<meta charset="utf-8">
<title>Kestrel Chiropractic — Business Card</title>
<link rel="stylesheet" href="https://fonts.googleapis.com/css2?family=Cinzel:wght@500&family=Exo+2:wght@400;500&display=swap">
<style>
  :root {
    --page: #1c1c1e;
    --card-black: #0f0f10;
    --card-white: #ffffff;
    --ink-dark: #2b2b2b;
    --ink-grey: #5a5a5a;
    --band-grey: #6b6b6b;
    --accent-blue: #3f7fd6;
    --text-light: #f4f4f4;
  }
  * { box-sizing: border-box; margin: 0; padding: 0; }
  html, body { width: 1200px; height: 900px; overflow: hidden; }
  body {
    background: var(--page);
    position: relative;
    font-family: "Exo 2", sans-serif;
  }
  .card {
    position: absolute;
    left: 250px;
    width: 700px;
    height: 400px;
    overflow: hidden;
    box-shadow: 0 12px 30px rgba(0,0,0,0.45);
  }
  /* Back side */
  .card-back { top: 25px; background: var(--card-black); }
  .card-back .texture {
    position: absolute; inset: 0;
    background: radial-gradient(circle at 50% 45%, #1b1b1d 0%, #111112 70%);
  }
  .card-back .brand {
    position: absolute;
    left: 0; right: 0; top: 250px;
    display: flex; justify-content: center; align-items: center; gap: 14px;
  }
  .brand-dot {
    width: 18px; height: 18px;
    background: var(--accent-blue);
  }
  .brand-name {
    font-family: "Cinzel", serif;
    font-weight: 500;
    letter-spacing: 1px;
    line-height: 1;
  }
  .card-back .brand-name { color: var(--text-light); font-size: 26px; }

  /* Front side */
  .card-front { top: 475px; background: var(--card-white); }
  .card-front .brand {
    position: absolute; left: 34px; top: 44px;
    display: flex; align-items: center; gap: 12px;
  }
  .card-front .brand-name { color: var(--ink-dark); font-size: 28px; }
  .holder {
    position: absolute; right: 40px; top: 118px; text-align: right;
  }
  .holder-name {
    font-family: "Cinzel", serif;
    font-weight: 500;
    font-size: 26px;
    color: var(--ink-grey);
    letter-spacing: 1px;
  }
  .holder-role {
    font-size: 19px;
    color: var(--accent-blue);
    margin-top: 2px;
  }
  .wave { position: absolute; left: 0; top: 0; width: 700px; height: 400px; }
  .contact {
    position: absolute; right: 34px; bottom: 28px;
    list-style: none;
    color: var(--text-light);
    font-size: 20px;
    text-align: right;
  }
  .contact li {
    display: flex; justify-content: flex-end; align-items: center; gap: 12px;
    line-height: 32px;
  }
  .contact .hl { color: var(--accent-blue); }
  .contact svg { width: 20px; height: 20px; flex: none; }
</style>
</head>
<body>

<section class="card card-back" aria-label="Card back">
  <div class="texture" role="img" aria-label="Dark repeating brand texture"></div>
  <div class="brand">
    <span class="brand-name">KESTREL CHIROPRACTIC</span>
  </div>
</section>

<section class="card card-front" aria-label="Card front">
  <svg class="wave" viewBox="0 0 700 400" aria-hidden="true">
    <path fill="var(--band-grey)" d="M0,282 C140,322 330,300 480,252 C580,220 650,200 700,198 L700,214 C640,216 570,236 480,266 C330,316 150,336 0,302 Z"/>
    <path fill="var(--band-grey)" d="M40,270 C160,292 300,290 420,262 C330,300 170,302 40,276 Z"/>
    <path fill="var(--card-black)" d="M0,318 C160,352 330,330 480,282 C580,250 650,232 700,230 L700,400 L0,400 Z"/>
  </svg>

  <div class="brand">
    <span class="brand-dot"></span>
    <span class="brand-name">KESTREL CHIROPRACTIC</span>
  </div>

  <div class="holder">
    <p class="holder-name">DANIEL HART</p>
    <p class="holder-role">Training Specialist</p>
  </div>

  <ul class="contact">
    <li>555.014.2876
      <svg viewBox="0 0 24 24" fill="none" stroke="var(--accent-blue)" stroke-width="1.8"><circle cx="12" cy="12" r="10"/><path d="M8.5 7.5c0 4.5 3.5 8.5 8 8.5l1-2-2.5-1.2-1 1c-1.5-.7-2.8-2-3.5-3.5l1-1L10.3 6.8z"/></svg>
    </li>
    <li>d.hart@kestrelchiro.com
      <svg viewBox="0 0 24 24" fill="none" stroke="var(--accent-blue)" stroke-width="1.8"><rect x="3" y="6" width="18" height="12" rx="1"/><path d="M3 7l9 6 9-6"/></svg>
    </li>
    <li><span>www.<span class="hl">kestrelchiro</span>.com</span>
      <svg viewBox="0 0 24 24" fill="none" stroke="var(--accent-blue)" stroke-width="1.8"><circle cx="12" cy="12" r="9.5"/><ellipse cx="12" cy="12" rx="4" ry="9.5"/><path d="M2.5 12h19M4 7h16M4 17h16"/></svg>
    </li>
  </ul>
</section>

</body>
</html>
```